Advertising agency needs site design

You will be designing a clean (plenty of white space) and vivid (colorful) design that is for an advertising agency named Pixel Harbor. Their current web site is located at www.PixelHarbor.net. From there you can see their services and get a feel for the company as the site stands today.
The following are direct quotes from the client:
“I want a clean look with colors of the teal blue, deep yellow (in logo) and then a good energetic orange (deep orange - rich) should bring a good feel and enthusiasm.”
“The orange can be a nice accent color, not dominant.”
“Saw two other things I like - the website lanternfoxstudio.com was pretty cool. I liked how the top banner changed colors as you moved to different tabs. I am somewhat wanting the colors I mentioned - like the blue color we use can be lighter as long as it works with the logo. - love the tidal frames site. I want quirky, creative and clean look - fun feel but slightly sophisticated to work with the medical field.”
Pixel Harbor currently focuses on the following primary industries:
• Medical / Health Care – Currently the primary industry
• Retail Industry
• Automotive Industry
• Entertainment Industry
Primary Services
• Media Planning & Buying: Web, TV, Print, Radio
• Campaign monitoring and reporting
• Commercial Production: TV & Radio
• Strategic Planning
• Market Research
• Internet Marketing: Email, SEO, Web design / development
Primary Navigation will consist of the following:
• Home
• About Us
o History
o Principal Profile (sub nav)
o Sales Team & Partners
• Clients
• Services
• Testimonials
• Contact Us
They want the web site to act as a basis for future marketing collateral so the overall feel from the web site must be capable of translating to print and other collateral. I do not currently have a clean digital version of their logo however their logo is on the web site (pixelharbor.net)
Target Market(s)
larger companies that are purchasing air time on television and radio. Typically in the health care industry and others described above in brief.
Industry/Entity Type
Advertising
Look and feel

```html
<!DOCTYPE html>
<html lang="en">
<head>
<meta charset="utf-8">
<title>Pixel Harbor – Home</title>
<link href="https://fonts.googleapis.com/css2?family=Arimo:wght@400;700&family=Cinzel:wght@600&family=Crimson+Text:ital@1&display=swap" rel="stylesheet">
<style>
:root{
  --teal:#1a6f93;
  --sky:#4b9fce;
  --orange:#e0661c;
  --amber:#f79a0b;
  --navy:#0f3550;
  --navy-deep:#0b2a42;
  --ink:#555;
  --line:#d6d6d6;
  --gold:#f1b324;
  --cat-health:#1ba7a7;
  --cat-retail:#6bb02b;
  --cat-auto:#d9450d;
  --cat-fun:#6c2f90;
}
*{box-sizing:border-box;margin:0;padding:0}
html,body{width:963px;height:1200px;overflow:hidden}
body{position:relative;font-family:"Arimo",Arial,sans-serif;color:var(--ink);background:var(--sky)}
ul{list-style:none}
.abs{position:absolute}

.header{left:0;top:0;width:963px;height:100px;background:linear-gradient(#fff,#f1f1f1)}
.logo{left:60px;top:30px;display:flex;align-items:center;gap:10px;font-size:34px;font-weight:400;color:var(--teal);letter-spacing:1px}
.logo .dot{width:14px;height:14px;border-radius:50%;background:var(--gold)}
.account{right:52px;top:12px;font-size:11px;font-weight:700;color:var(--teal);letter-spacing:.5px}
.call{left:658px;top:22px;width:218px;height:68px;background:#fff;border-radius:6px;box-shadow:0 2px 5px rgba(0,0,0,.2)}
.call .agent{position:absolute;left:4px;bottom:6px;width:56px;height:64px;border-radius:6px;background:linear-gradient(#e07a3a,#b03a1a)}
.call .label{position:absolute;left:72px;top:18px;font-size:13px;font-weight:700;color:var(--teal)}
.call .num{position:absolute;left:72px;top:34px;font-size:20px;font-weight:700;color:var(--teal)}

.nav{left:0;top:100px;width:963px;height:36px;background:linear-gradient(#fff,#eceef0);border-top:1px solid var(--line);border-bottom:1px solid var(--line)}
.nav ul{display:flex;margin-left:44px;height:100%}
.nav li{padding:0 20px;line-height:34px;font-size:13px;color:var(--teal);border-right:1px solid var(--line)}
.search{left:705px;top:107px;width:200px;height:25px;background:#fff;border:1px solid var(--line);font-size:11px;color:#999;padding:6px 8px}
.search svg{position:absolute;right:6px;top:4px}

.band{left:0;top:136px;width:963px;height:263px;background:var(--orange)}
.panel{left:44px;top:146px;width:876px;height:820px;background:#fff;border-radius:6px;box-shadow:0 0 6px rgba(0,0,0,.25)}
.hero{left:50px;top:150px;width:865px;height:282px;background:linear-gradient(100deg,#2f6a8e 0%,#4a8fb3 45%,#9fc8de 75%,#d7e8f0 100%);border-bottom:4px solid #cfe2ec}
.hero h1{position:absolute;left:40px;top:70px;font-family:"Cinzel",serif;font-weight:600;font-size:28px;color:var(--gold)}
.hero p{position:absolute;left:40px;top:110px;width:380px;font-family:"Crimson Text",serif;font-style:italic;font-size:22px;line-height:27px;color:#fff}

.cats{left:53px;top:448px;display:flex;gap:10px}
.cat{position:relative;width:207px;height:40px;border-radius:4px;color:#fff;font-size:16px;line-height:40px;padding-left:12px}
.cat svg{position:absolute;right:6px;top:4px}
.c1{background:var(--cat-health)}.c2{background:var(--cat-retail)}.c3{background:var(--cat-auto)}.c4{background:var(--cat-fun)}

.welcome{left:53px;top:508px;width:548px}
.welcome h2{font-size:18px;font-weight:400;color:#555;margin-bottom:14px}
.welcome h2 span{color:var(--teal)}
.welcome p{font-size:11px;line-height:19.5px;letter-spacing:.2px}
.services{left:659px;top:508px;width:252px}
.services h2{font-size:18px;font-weight:400;color:#666;margin-bottom:14px}
.services li{height:24px;margin-bottom:3px;background:#eef0ec;font-size:12px;line-height:24px;padding-left:26px;position:relative;color:#444}
.services li::before{content:"";position:absolute;left:8px;top:8px;border:4px solid transparent;border-left:5px solid var(--teal)}

.lower{left:44px;top:718px;width:876px;height:247px;background:var(--amber);border-radius:0 0 6px 6px}
.lower h3{font-size:16px;font-weight:400;line-height:20px;color:#222;position:absolute}
.news{left:10px;top:6px;width:232px}
.news .item{border-bottom:1px dashed #fff;padding:6px 2px 6px;color:#fff;font-size:11px;line-height:16px}
.news .item b{display:block;font-size:11px}
.news .more{text-align:right;font-size:10px;line-height:12px;font-weight:700;color:#222;margin-top:6px}
.quote{left:316px;top:33px;width:218px;height:128px;background:#fff;border-radius:18px;padding:18px 16px 0 26px;font-size:11px;line-height:16px;color:#555}
.quote::before{content:"\201C";position:absolute;left:10px;top:6px;font-size:24px;color:#333}
.quote-tail{left:344px;top:158px}
.author{left:336px;top:186px;font-size:11px;line-height:20px;color:#555}
.author b{color:var(--teal);font-style:italic}
.pager{font-size:12px;font-weight:700;color:#222}
.news-form{left:644px;top:6px;width:222px}
.news-form .tip{color:#fff;font-size:11px;margin:32px 0 0 6px}
.news-form .field{margin-top:8px;height:28px;background:#fff;border-radius:4px;font-size:11px;color:#999;padding:8px 10px}
.submit{left:778px;top:92px;width:84px;height:26px;background:#333;border-radius:4px;color:#fff;font-size:13px;font-weight:700;text-align:center;line-height:26px;letter-spacing:1px}
.clients-box{left:656px;top:148px;width:196px;height:72px;background:#fff;border-radius:8px;border:3px solid #eee;text-align:center;font-size:17px;font-weight:700;color:#222;line-height:26px;padding-top:10px;letter-spacing:1px}

.footer{left:44px;top:965px;width:876px;height:235px;background:var(--navy)}
.footer h4{font-size:12px;font-weight:700;color:#fff;letter-spacing:.5px;margin-bottom:14px}
.fcol{position:absolute;top:14px}
.fcol li{font-size:11px;color:#e6edf2;line-height:21px;padding-left:14px;position:relative}
.fcol li::before{content:"";position:absolute;left:2px;top:9px;width:3px;height:3px;background:#fff}
.fcol.follow li{padding-right:36px}
.fcol.follow li i{position:absolute;right:0;top:5px;width:11px;height:11px;border-radius:2px}
.contact p{font-size:11px;color:#e6edf2;line-height:18px}
.contact .ph{display:flex;align-items:center;gap:10px;margin-top:6px}
.copy{left:0;bottom:0;width:876px;height:46px;background:var(--navy-deep);text-align:center;font-size:11px;color:#cfd9e0;line-height:40px;letter-spacing:.5px}
</style>
</head>
<body>

<header class="abs header">
  <div class="abs logo"><span>Pixel Harbor</span><span class="dot"></span></div>
  <div class="abs account">LOGIN &nbsp;|&nbsp; SIGN UP</div>
  <div class="abs call">
    <div class="agent" role="img" aria-label="Illustration of a support agent wearing a headset"></div>
    <div class="label">CALL US</div>
    <div class="num">555 014 2288</div>
  </div>
</header>

<nav class="abs nav">
  <ul><li>Home</li><li>About Us</li><li>Clients</li><li>Services</li><li>Testimonials</li><li>Contact Us</li></ul>
</nav>
<div class="abs search">Search
  <svg width="16" height="16" viewBox="0 0 16 16"><circle cx="6.5" cy="6.5" r="4.5" fill="none" stroke="#1a6f93" stroke-width="2"/><line x1="10" y1="10" x2="14" y2="14" stroke="#1a6f93" stroke-width="2.5"/></svg>
</div>

<div class="abs band"></div>
<div class="abs panel"></div>

<section class="abs hero" role="img" aria-label="Banner photo of a smiling businesswoman over a close-up of a blue eye">
  <h1>LOREM IPSUM DOLOR SIT</h1>
  <p>Lorem ipsum dolor sit amet, consectetuer adipiscing elit. Aenean commodo l igula eget dolor.</p>
</section>

<div class="abs cats">
  <div class="cat c1">Medical / Health<svg width="28" height="32" viewBox="0 0 28 32"><path d="M2 30 C14 30 12 2 26 2" fill="none" stroke="#fff" stroke-width="1.5"/><path d="M22 24h6M25 21v6" stroke="#fff" stroke-width="1.5"/></svg></div>
  <div class="cat c2">Retail<svg width="28" height="32" viewBox="0 0 28 32"><path d="M2 30 C14 30 12 2 26 2" fill="none" stroke="#fff" stroke-width="1.5"/><path d="M22 24h6M25 21v6" stroke="#fff" stroke-width="1.5"/></svg></div>
  <div class="cat c3">Automotive<svg width="28" height="32" viewBox="0 0 28 32"><path d="M2 30 C14 30 12 2 26 2" fill="none" stroke="#fff" stroke-width="1.5"/><path d="M22 24h6M25 21v6" stroke="#fff" stroke-width="1.5"/></svg></div>
  <div class="cat c4">Entertainment<svg width="28" height="32" viewBox="0 0 28 32"><path d="M2 30 C14 30 12 2 26 2" fill="none" stroke="#fff" stroke-width="1.5"/><path d="M22 24h6M25 21v6" stroke="#fff" stroke-width="1.5"/></svg></div>
</div>

<section class="abs welcome">
  <h2>Welcome to <span>Pixel Harbor</span></h2>
  <p>Lorem ipsum dolor sit amet, consectetuer adipiscing elit. Aenean commodo ligula eget dolor. Aenean massa. Cum sociis natoque penatibus et magnis dis parturient montes, nascetur ridiculus mus. Donec quam felis, ultricies nec, pellentesque eu, pretium quis, sem. Nulla consequat massa quis enim. Donec pede justo, fringilla vel, aliquet nec, vulputate eget, arcu.Lorem ipsum dolor sit amet, consectetuer adipiscing elit. Aenean commodo ligula eget dolor. Aenean massa. Cum sociis natoque penatibus et magnis dis parturient montes, nascetur ridiculus mus. Donec quam felis, ultricies nec, pellentesque eu, pretium quis, sem. Nulla consequat massa quis enim. Donec pede justo, fringilla vel, aliquet nec, vulputate eget, arcu.n commodo ligula eget dolor. Aenean massa.</p>
</section>

<aside class="abs services">
  <h2>Services</h2>
  <ul>
    <li>Media Planning &amp; Buying</li>
    <li>Campaign monitoring and reporting</li>
    <li>Commercial Production</li>
    <li>Strategic Planning</li>
    <li>Market Research</li>
    <li>Internet Marketing</li>
  </ul>
</aside>

<section class="abs lower">
  <div class="abs news">
    <h3 style="position:static">News</h3>
    <div class="item"><b>MAY 19, 2011</b>Lorem ipsum dolor sit ametconsectetuer adipiscing elit. Aenean</div>
    <div class="item"><b>MAY 19, 2011</b>Lorem ipsum dolor sit ametconsectetuer adipiscing elit. Aenean</div>
    <div class="item"><b>MAY 19, 2011</b>Lorem ipsum dolor sit ametconsectetuer adipiscing elit. Aenean</div>
    <div class="more">Read more &gt;&gt;</div>
  </div>

  <h3 style="left:316px;top:6px">Testimonials</h3>
  <div class="abs quote">Lorem ipsum dolor sit ametcon-sectetuer adipiscing elit. Aenean commodo ligula eget doloAenean massa. Cum eget doloAenean massa. Cum sociis sociis</div>
  <svg class="abs quote-tail" width="26" height="24" viewBox="0 0 26 24"><path d="M0 0H26L4 24Z" fill="#fff"/></svg>
  <div class="abs pager" style="left:500px;top:170px">&lt; &gt;</div>
  <div class="abs author"><b>Name</b>, art director<br>mara.lindqvist@examplemail.com</div>

  <h3 style="left:640px;top:6px">Newsletter</h3>
  <div class="abs news-form">
    <div class="tip">Sign up for our Newsletters</div>
    <div class="field">Enter you email</div>
  </div>
  <div class="abs submit">SUBMIT</div>
  <h3 style="left:650px;top:117px">Our Clients</h3>
  <div class="abs clients-box">HERE COMES LOGO<br>CLIENTS</div>
  <div class="abs pager" style="left:824px;top:226px">&lt; &gt;</div>
</section>

<footer class="abs footer">
  <div class="fcol" style="left:12px">
    <h4>Company</h4>
    <ul><li>Home</li><li>About Us</li><li>Contact Us</li><li>Privacy Policy</li><li>Tearms of use</li></ul>
  </div>
  <div class="fcol" style="left:145px">
    <h4>Industries</h4>
    <ul><li>Medical / Health Care</li><li>Retail</li><li>Automotive</li><li>Entertainment</li></ul>
  </div>
  <div class="fcol" style="left:317px">
    <h4>Services</h4>
    <ul><li>Media Planning &amp; Buying C</li><li>Campaign monitoring and reporting</li><li>Commercial Production</li><li>Strategic Planning</li><li>Market Research</li><li>Internet Marketing</li></ul>
  </div>
  <div class="fcol follow" style="left:556px">
    <h4>Follow Us</h4>
    <ul>
      <li>Rss<i style="background:#f08a1c"></i></li>
      <li>Chirper<i style="background:#6fc6e4"></i></li>
      <li>Friendbook<i style="background:#3b5a9a"></i></li>
    </ul>
  </div>
  <div class="fcol contact" style="left:694px">
    <h4>Contact Us</h4>
    <p>Pixel Harbor, Inc.<br>4820 Cedar Loop, Suite 310<br>Brookfield, Texas 75099</p>
    <div class="ph"><svg width="16" height="12" viewBox="0 0 16 12"><path d="M1 4C1 1 15 1 15 4L12 5 11 3H5L4 5Z" fill="#fff"/><rect x="4" y="6" width="8" height="6" rx="1" fill="#fff"/></svg><p>555.201.4471 &nbsp;(P)</p></div>
    <div class="ph" style="margin-top:2px"><svg width="16" height="14" viewBox="0 0 16 14"><rect x="4" y="0" width="8" height="4" fill="#fff"/><rect x="1" y="4" width="14" height="6" rx="1" fill="#fff"/><rect x="4" y="9" width="8" height="5" fill="#ccc"/></svg><p>555.201.4472 &nbsp;(F)</p></div>
  </div>
  <div class="abs copy">2011 © pixelharbor.com. All rights reserved.</div>
</footer>

</body>
</html>
```